Naturopath Practitioner Card Design

I am a naturopath needing a design for a business card mainly to show that I am a naturopath and have some contact details to give to prospective clients. I am open minded about the design and what is on the second side of the card whether it just be some artwork or space for details, appointment times etc. Naturopathy is the practice of natural medicine that uses a holistic approach and incorporates herbal and nutritional medicine.

Industry/Entity Type

Business

Contact Information for Business Card

Tom Rudd NaturopathBHSc (Naturopathy) Member WHPG 0487 925 316 tom.rudd@mailexample.com www.tomruddnaturopathy.example.au

Requirements
Nice to have
• Would prefer some kind of original pattern/art work/logo rather than an image, not fussed if its very simple/basic
• I am open to any colour but think I would prefer a more earthy sandy clay etc type style than the greens that are commonly associated with naturopathy.
Should not have
• Don't really want to have generic stock images on it

```html
<!DOCTYPE html>
<html lang="en">
<head>
<meta charset="utf-8">
<title>Tom Rudd Naturopath – Business Card</title>
<link rel="stylesheet" href="https://fonts.googleapis.com/css2?family=Arimo&family=Tinos&display=swap">
<style>
  :root {
    --page-bg: #2a2a2a;
    --card-deep: #2f4a12;
    --card-mid: #4f7a1f;
    --leaf-light: #a9cf6a;
    --leaf-mid: #6e9e2c;
    --front-text: #ffffff;
    --back-bg: #efefef;
    --back-ink: #2c3d0b;
    --back-body: #1b1b1b;
  }
  * { margin: 0; padding: 0; box-sizing: border-box; }
  html, body { width: 1200px; height: 800px; overflow: hidden; }
  body { background: var(--page-bg); position: relative; font-family: "Arimo", Arial, sans-serif; }

  .card {
    position: absolute;
    top: 247px;
    width: 536px;
    height: 305px;
    overflow: hidden;
  }
  .card-front { left: 48px; }
  .card-back { left: 616px; background: var(--back-bg); }

  /* Front */
  .front-art { position: absolute; inset: 0; }
  .front-name {
    position: absolute; left: 17px; top: 145px;
    font-family: "Tinos", "Times New Roman", serif;
    font-size: 35px; color: var(--front-text); line-height: 1;
  }
  .front-role {
    position: absolute; left: 16px; top: 183px;
    font-size: 19px; line-height: 21.5px; color: var(--front-text);
  }
  .contact-list {
    position: absolute; right: 20px; top: 250px;
    list-style: none; font-size: 17px; line-height: 21px; color: var(--front-text);
  }
  .contact-item { display: flex; align-items: center; justify-content: flex-end; gap: 9px; }
  .contact-icon { width: 11px; height: 11px; }

  /* Back */
  .back-title {
    position: absolute; left: 0; right: 0; top: 37px; text-align: center;
    padding-left: 4px;
    font-family: "Tinos", "Times New Roman", serif;
    font-size: 39px; color: var(--back-ink); line-height: 1;
  }
  .field-label {
    position: absolute; font-size: 18px; color: var(--back-ink); line-height: 1;
  }
  .dotted-line {
    position: absolute; height: 0; border-top: 2px dotted var(--back-body);
  }
  .day-list {
    position: absolute; top: 186px; left: 0; right: 0; list-style: none;
  }
  .day-option {
    position: absolute; display: flex; align-items: center; gap: 5px;
    font-size: 16.5px; color: var(--back-body); line-height: 1;
  }
  .day-box {
    width: 15px; height: 15px; border: 1.6px solid var(--back-body); border-radius: 2px;
  }
</style>
</head>
<body>

<section class="card card-front" aria-label="Business card front">
  <svg class="front-art" width="536" height="305" viewBox="0 0 536 305">
    <defs>
      <linearGradient id="frontBase" x1="0" y1="0" x2="0" y2="1">
        <stop offset="0" stop-color="#3d5f16"/>
        <stop offset="1" stop-color="var(--card-deep)"/>
      </linearGradient>
      <linearGradient id="leafTone" x1="0" y1="0" x2="1" y2="1">
        <stop offset="0" stop-color="var(--leaf-light)"/>
        <stop offset="0.55" stop-color="var(--leaf-mid)"/>
        <stop offset="1" stop-color="#86b545"/>
      </linearGradient>
    </defs>
    <rect width="536" height="305" fill="url(#frontBase)"/>
    <g role="img" aria-label="Close-up photograph of a green leaf covered in water droplets">
      <path d="M0 0 H536 V150 C500 175 440 190 380 170 C300 145 240 100 150 85 C90 75 40 80 0 95 Z" fill="url(#leafTone)"/>
    </g>
  </svg>

  <h1 class="front-name">Tom Rudd</h1>
  <p class="front-role">Naturopath<br>BHSc (Naturopathy) Member WHPG</p>

  <ul class="contact-list">
    <li class="contact-item">
      <span>0487 925 316</span>
      <svg class="contact-icon" viewBox="0 0 11 11" aria-hidden="true">
        <rect width="11" height="11" rx="1" fill="#fff"/>
        <path d="M2.5 4 Q5.5 2 8.5 4 L8 5 L6.8 4.6 V4.1 H4.2 V4.6 L3 5 Z M3.5 6 H7.5 V8.5 H3.5 Z" fill="var(--card-deep)"/>
      </svg>
    </li>
    <li class="contact-item">
      <span>tom.rudd@mailexample.com</span>
      <svg class="contact-icon" viewBox="0 0 11 11" aria-hidden="true">
        <rect width="11" height="11" rx="1" fill="#fff"/>
        <rect x="2.5" y="3.5" width="6" height="4" fill="none" stroke="var(--card-deep)" stroke-width="1"/>
        <path d="M2.5 3.5 L5.5 6 L8.5 3.5" fill="none" stroke="var(--card-deep)" stroke-width="1"/>
      </svg>
    </li>
  </ul>
</section>

<section class="card card-back" aria-label="Appointment card back">
  <h2 class="back-title">Appointment</h2>

  <span class="field-label" style="left:22px; top:106px;">For:</span>
  <span class="dotted-line" style="left:75px; width:428px; top:119px;"></span>

  <span class="field-label" style="left:21px; top:144px;">Date:</span>
  <span class="dotted-line" style="left:76px; width:161px; top:157px;"></span>
  <span class="field-label" style="left:246px; top:145px;">Time:</span>
  <span class="dotted-line" style="left:295px; width:208px; top:157px;"></span>

  <ul class="day-list">
    <li class="day-option" style="left:22px;"><span class="day-box"></span>MON.</li>
    <li class="day-option" style="left:108px;"><span class="day-box"></span>TUE.</li>
    <li class="day-option" style="left:191px;"><span class="day-box"></span>WED.</li>
    <li class="day-option" style="left:286px;"><span class="day-box"></span>THUR.</li>
    <li class="day-option" style="left:379px;"><span class="day-box"></span>FRI.</li>
    <li class="day-option" style="left:448px;"><span class="day-box"></span>SAT.</li>
  </ul>

  <span class="dotted-line" style="left:23px; width:476px; top:266px;"></span>
</section>

</body>
</html>
```